Verdant Ledger - Paid Surveys publisher portal

• Homepage
• Blank Sub Page (Where content goes in between the header/footer)
• Publisher Application Page, complete with Form
• Survey Wall page

Sites that are in a similar vertical that have interesting designs:
rovabin.com
quillmarsh.com
dovek.com
tarn.io

This is a business-to-business site, and needs to have this type of feel to it. Focus on generating revenue, offer completion, paid surveys is the market.

Format: HTML/CSS

Link to current version of application, and form:
https://gridwaveform.brokelqest.com
https://gridwaveform.brokelqest.com/apply
https://gridwaveform.brokelqest.com/panel/4/morvath_user

Please note that we are changing the brand of this project, the name will be determined shortly but everything else remains. It will likely be Verdant Ledger instead of GridWaveform. We will confirm.

Industry/Entity Type

Market Research

Coding

Coded - Design and coding required

Number of Pages Required

4 page

Font styles to use
Sans Serif

Colors

Designer to choose colors to be used in the design.

```html
<!DOCTYPE html>
<html lang="en">
<head>
<meta charset="utf-8">
<title>GridWaveform – Home</title>
<link href="https://fonts.googleapis.com/css2?family=Poppins:wght@300;400;500;600;700&display=swap" rel="stylesheet">
<style>
:root{
  --red:#f04e45;
  --ink:#2b2b2b;
  --text:#3a3a3a;
  --muted:#f0f0f0;
  --footer:#333333;
  --white:#ffffff;
}
*{box-sizing:border-box;margin:0;padding:0}
html,body{width:1200px;height:3267px;overflow:hidden}
body{font-family:"Poppins",sans-serif;color:var(--text);background:var(--white);position:relative}
.abs{position:absolute}
.btn{position:absolute;background:var(--red);color:var(--white);border-radius:30px;font-weight:600;display:flex;align-items:center;justify-content:center}
/* hero */
.hero{left:0;top:0;width:1200px;height:762px;background:linear-gradient(180deg,#3d3935 0%,#5a524a 45%,#3a3632 100%);clip-path:polygon(0 0,100% 0,100% 653px,0 762px)}
.hero-shade{left:0;top:0;width:1200px;height:762px;background:rgba(0,0,0,.35);clip-path:polygon(0 0,100% 0,100% 653px,0 762px)}
.brand{left:92px;top:56px;display:flex;align-items:center;gap:12px;color:var(--white);font-size:31px;font-weight:600}
.brand-dot{width:44px;height:44px;border-radius:50%;background:var(--red)}
.nav{right:91px;top:68px;display:flex;gap:22px;font-size:15px;font-weight:500;color:var(--white)}
.nav .active{color:var(--red)}
.hero-kicker{left:0;width:1200px;top:225px;text-align:center;color:var(--white);font-size:45px;font-weight:300}
.hero-title{left:0;width:1200px;top:280px;text-align:center;color:var(--white);font-size:60px;font-weight:700;letter-spacing:1px}
.hero-input{left:298px;top:394px;width:340px;height:53px;border-radius:30px;background:var(--white);color:#999;font-size:13px;padding-left:24px;display:flex;align-items:center}
.hero-btn{left:651px;top:394px;width:249px;height:53px;font-size:17px}
.watch{left:0;width:1200px;top:486px;display:flex;justify-content:center;align-items:center;gap:12px;color:var(--white);font-size:25px;font-weight:500}
.side{color:var(--white);font-size:15px;font-weight:600;display:flex;flex-direction:column;gap:10px;text-align:center;width:16px}
.dots{left:566px;top:662px;display:flex;gap:12px}
.dots span{width:9px;height:9px;border-radius:50%;background:var(--white);opacity:.8}
.dots span:first-child{opacity:1}
.dots-line{left:570px;top:676px;width:2px;height:40px;background:var(--red)}
/* shared */
.photo{position:absolute}
h2.sec{position:absolute;color:var(--red);font-size:34px;font-weight:700;letter-spacing:.5px}
.center{left:0;width:1200px;text-align:center}
.lead{position:absolute;left:170px;width:860px;text-align:center;font-size:15px;line-height:30px;color:var(--text)}
.band{position:absolute;left:0;width:1200px;background:var(--muted)}
/* about */
.about-copy{left:610px;top:880px;width:490px;font-size:14px;line-height:30px}
/* services */
.card{position:absolute;background:var(--white);box-shadow:0 1px 4px rgba(0,0,0,.08);text-align:center}
.svc h3{color:var(--red);font-size:20px;font-weight:700;margin-top:14px}
.svc p{font-size:14px;line-height:26px;margin:14px 30px 0}
.svc svg{margin-top:22px}
/* affiliates */
.aff-copy{left:126px;top:1850px;width:480px;font-size:15px;line-height:30px}
.ticks{left:126px;top:1915px;list-style:none;font-size:15px;line-height:30px}
.ticks li{display:flex;align-items:center;gap:8px}
.tick{width:15px;height:15px;background:var(--red);border-radius:2px;display:flex;align-items:center;justify-content:center}
/* blog */
.post .thumb{position:absolute;left:17px;top:18px;width:273px;height:180px}
.post h3{position:absolute;left:17px;top:212px;color:var(--red);font-size:20px;font-weight:700}
.meta{position:absolute;left:17px;display:flex;align-items:center;gap:8px;font-size:15.5px;color:var(--ink);font-weight:500}
.post p{position:absolute;left:17px;top:320px;width:280px;text-align:left;font-size:11.5px;line-height:22px}
.post .btn{left:17px;top:397px;width:80px;height:28px;font-size:12px}
/* footer */
.footer{left:0;top:2908px;width:1200px;height:359px;background:var(--footer);color:var(--white)}
.fcol{position:absolute;top:60px}
.fcol h4{font-size:23px;font-weight:600;margin-bottom:18px}
.fcol ul{list-style:none;font-size:13px;line-height:30px}
.fcol li{display:flex;align-items:center;gap:10px}
.sub-input{width:275px;height:33px;background:var(--white);font-size:11px;color:#999;padding-left:10px;display:flex;align-items:center;margin-top:16px}
.copyright{left:0;width:1200px;top:316px;text-align:center;font-size:13px}
.social{top:316px;width:26px;height:26px;border-radius:50%}
</style>
</head>
<body>

<!-- Hero -->
<div class="abs hero" role="img" aria-label="Photo of a smiling business team standing together in an office"></div>
<div class="abs hero-shade"></div>
<div class="abs brand"><span class="brand-dot"></span>GridWaveform</div>
<nav class="abs nav"><span class="active">HOME</span><span>ABOUT US</span><span>OUR SERVICES</span><span>BLOG</span><span>CONTACT US</span></nav>
<div class="abs side" style="left:46px;top:325px"><span>P</span><span>R</span><span>E</span><span>V</span></div>
<div class="abs side" style="left:1140px;top:325px"><span>N</span><span>E</span><span>X</span><span>T</span></div>
<div class="abs hero-kicker">Welcome to</div>
<div class="abs hero-title">GRIDWAVEFORM</div>
<div class="abs hero-input">Your email address</div>
<div class="btn hero-btn">GET STARTED</div>
<div class="abs watch">
  <svg width="26" height="26" viewBox="0 0 26 26"><circle cx="13" cy="13" r="13" fill="#fff"/><path d="M10 7l9 6-9 6z" fill="#3d3935"/></svg>Watch Video
</div>
<div class="abs dots"><span></span><span></span><span></span><span></span></div>
<div class="abs dots-line"></div>

<!-- About -->
<div class="photo" style="left:111px;top:821px;width:473px;height:316px;background:linear-gradient(135deg,#6b6b6b,#c9c9c9 55%,#8a8a8a)" role="img" aria-label="Photo of a desk with charts, a laptop and hands reviewing reports"></div>
<h2 class="sec" style="left:610px;top:830px">ABOUT US</h2>
<p class="abs about-copy">Sed ut perspiciatis unde omnis iste natus error sit voluptatem accusantium doloremque laudantium, totam rem aperiam, eaque ipsa quae ab illo inventore veritatis et quasi architecto beatae vitae dicta sunt explicabo. Nemo enim ipsam voluptatem quia voluptas sit aspernatur aut odit aut fugit, sed quia consequuntur magni dolores eos qui ratione voluptatem sequi nesciunt.</p>
<div class="btn" style="left:610px;top:1074px;width:109px;height:39px;font-size:15px">Read More</div>

<!-- Services -->
<div class="band" style="top:1200px;height:490px"></div>
<h2 class="sec center" style="top:1254px">OUR SERVICES</h2>
<p class="lead" style="top:1314px">Lorem ipsum dolor sit amet, consectetur adipiscing elit. Fusce aliquet, massa ac ornare feugiat, nunc dui auctor ipsum, sed posuere eros sapien id quam.</p>
<div class="card svc" style="left:115px;top:1398px;width:308px;height:225px">
  <svg width="60" height="54" viewBox="0 0 60 54" fill="none" stroke="#f04e45" stroke-width="3"><path d="M3 2v49h55"/><path d="M10 42l12-18 10 10 10-12 12 10"/><circle cx="22" cy="24" r="3"/><circle cx="32" cy="34" r="3"/><circle cx="42" cy="22" r="3"/></svg>
  <h3>LOREM IPSUM DOLOR</h3>
  <p>Lorem ipsum dolor sit amet, consectetur adipiscing elit. Fusce aliquet, massa ac ornare.</p>
</div>
<div class="card svc" style="left:451px;top:1398px;width:307px;height:225px">
  <svg width="54" height="54" viewBox="0 0 54 54" fill="none" stroke="#f04e45" stroke-width="3"><rect x="8" y="3" width="38" height="48" rx="2"/><path d="M16 14h22M16 24h22M16 34h22M16 44h14"/></svg>
  <h3>LOREM IPSUM DOLOR</h3>
  <p>Lorem ipsum dolor sit amet, consectetur adipiscing elit. Fusce aliquet, massa ac ornare.</p>
</div>
<div class="card svc" style="left:784px;top:1398px;width:307px;height:225px">
  <svg width="46" height="54" viewBox="0 0 46 54" fill="none" stroke="#f04e45" stroke-width="3"><rect x="4" y="7" width="38" height="44" rx="3"/><rect x="15" y="2" width="16" height="9" rx="2"/><path d="M11 22h4M20 22h15M11 32h4M20 32h15M11 42h4M20 42h15"/></svg>
  <h3>LOREM IPSUM DOLOR</h3>
  <p>Lorem ipsum dolor sit amet, consectetur adipiscing elit. Fusce aliquet, massa ac ornare.</p>
</div>

<!-- Affiliates -->
<h2 class="sec" style="left:126px;top:1784px">AFFILIATES</h2>
<p class="abs aff-copy">Sed ut perspiciatis unde omnis iste natus error sit voluptatem accusantium doloremque laudantium.</p>
<ul class="abs ticks">
  <li><span class="tick"><svg width="10" height="10" viewBox="0 0 10 10"><path d="M1.5 5l2.5 2.5 4.5-5" stroke="#fff" stroke-width="1.8" fill="none"/></svg></span>#1 Affiliate Manager</li>
  <li><span class="tick"><svg width="10" height="10" viewBox="0 0 10 10"><path d="M1.5 5l2.5 2.5 4.5-5" stroke="#fff" stroke-width="1.8" fill="none"/></svg></span>Custom Tracking Platform</li>
  <li><span class="tick"><svg width="10" height="10" viewBox="0 0 10 10"><path d="M1.5 5l2.5 2.5 4.5-5" stroke="#fff" stroke-width="1.8" fill="none"/></svg></span>Over 2,000 Live Offers</li>
  <li><span class="tick"><svg width="10" height="10" viewBox="0 0 10 10"><path d="M1.5 5l2.5 2.5 4.5-5" stroke="#fff" stroke-width="1.8" fill="none"/></svg></span>Guaranteed Top Payouts</li>
</ul>
<div class="btn" style="left:126px;top:2056px;width:124px;height:41px;font-size:15px">Read More</div>
<div class="abs" style="left:860px;top:1771px;width:249px;height:348px;background:var(--red);clip-path:polygon(0 0,100% 0,100% 100%,20% 100%,20% 8%,0 8%)"></div>
<div class="photo" style="left:653px;top:1790px;width:430px;height:307px;background:linear-gradient(135deg,#7a6a5e,#cfc4b8 60%,#9a8d80)" role="img" aria-label="Photo of two women reviewing papers at a restaurant table"></div>

<!-- Blog -->
<div class="band" style="top:2204px;height:704px"></div>
<h2 class="sec center" style="top:2258px">OUR BLOG</h2>
<p class="lead" style="top:2320px">Lorem ipsum dolor sit amet, consectetur adipiscing elit. Fusce aliquet, massa ac ornare feugiat, nunc dui auctor ipsum, sed posuere eros sapien id quam.</p>

<div class="card post" style="left:113px;top:2402px;width:307px;height:441px">
  <div class="thumb" style="background:linear-gradient(135deg,#6b6b6b,#c9c9c9 55%,#8a8a8a)" role="img" aria-label="Photo of a desk with charts and a laptop"></div>
  <h3>DUIS ULTRICIES ALIQUET</h3>
  <div class="meta" style="top:253px"><svg width="14" height="15" viewBox="0 0 14 15"><circle cx="7" cy="4" r="3.5" fill="#2b2b2b"/><path d="M0 15c0-4 3-6 7-6s7 2 7 6z" fill="#2b2b2b"/></svg>Admin&nbsp;&nbsp;<svg width="14" height="14" viewBox="0 0 14 14"><rect x="0" y="2" width="14" height="12" rx="1" fill="#2b2b2b"/><path d="M3 0v4M11 0v4" stroke="#2b2b2b" stroke-width="2"/></svg>08 Sep 2018</div>
  <div class="meta" style="top:287px"><svg width="15" height="14" viewBox="0 0 15 14"><ellipse cx="7.5" cy="6" rx="7.5" ry="6" fill="#2b2b2b"/><path d="M2 14l2-4 3 1z" fill="#2b2b2b"/></svg>5 Comments</div>
  <p>Lorem ipsum dolor sit amet, consectetur adipiscing elit. Fusce aliquet, massa ac ornare feugiat, nunc dui auctor ipsum</p>
  <div class="btn">Read More</div>
</div>
<div class="card post" style="left:449px;top:2402px;width:309px;height:441px">
  <div class="thumb" style="background:linear-gradient(135deg,#7a6a5e,#cfc4b8 60%,#9a8d80)" role="img" aria-label="Photo of two women reviewing papers at a restaurant table"></div>
  <h3>DUIS ULTRICIES ALIQUET</h3>
  <div class="meta" style="top:253px"><svg width="14" height="15" viewBox="0 0 14 15"><circle cx="7" cy="4" r="3.5" fill="#2b2b2b"/><path d="M0 15c0-4 3-6 7-6s7 2 7 6z" fill="#2b2b2b"/></svg>Admin&nbsp;&nbsp;<svg width="14" height="14" viewBox="0 0 14 14"><rect x="0" y="2" width="14" height="12" rx="1" fill="#2b2b2b"/><path d="M3 0v4M11 0v4" stroke="#2b2b2b" stroke-width="2"/></svg>08 Sep 2018</div>
  <div class="meta" style="top:287px"><svg width="15" height="14" viewBox="0 0 15 14"><ellipse cx="7.5" cy="6" rx="7.5" ry="6" fill="#2b2b2b"/><path d="M2 14l2-4 3 1z" fill="#2b2b2b"/></svg>5 Comments</div>
  <p>Lorem ipsum dolor sit amet, consectetur adipiscing elit. Fusce aliquet, massa ac ornare feugiat, nunc dui auctor ipsum</p>
  <div class="btn">Read More</div>
</div>
<div class="card post" style="left:785px;top:2402px;width:307px;height:441px">
  <div class="thumb" style="background:linear-gradient(135deg,#8c8c88,#e2e0dc 60%,#a5a29c)" role="img" aria-label="Photo of colleagues talking at a bright café table"></div>
  <h3>DUIS ULTRICIES ALIQUET</h3>
  <div class="meta" style="top:253px"><svg width="14" height="15" viewBox="0 0 14 15"><circle cx="7" cy="4" r="3.5" fill="#2b2b2b"/><path d="M0 15c0-4 3-6 7-6s7 2 7 6z" fill="#2b2b2b"/></svg>Admin&nbsp;&nbsp;<svg width="14" height="14" viewBox="0 0 14 14"><rect x="0" y="2" width="14" height="12" rx="1" fill="#2b2b2b"/><path d="M3 0v4M11 0v4" stroke="#2b2b2b" stroke-width="2"/></svg>08 Sep 2018</div>
  <div class="meta" style="top:287px"><svg width="15" height="14" viewBox="0 0 15 14"><ellipse cx="7.5" cy="6" rx="7.5" ry="6" fill="#2b2b2b"/><path d="M2 14l2-4 3 1z" fill="#2b2b2b"/></svg>5 Comments</div>
  <p>Lorem ipsum dolor sit amet, consectetur adipiscing elit. Fusce aliquet, massa ac ornare feugiat, nunc dui auctor ipsum</p>
  <div class="btn">Read More</div>
</div>

<!-- Footer -->
<footer class="abs footer">
  <div class="fcol" style="left:98px">
    <h4>Contact Us</h4>
    <ul>
      <li><svg width="10" height="13" viewBox="0 0 10 13"><path d="M5 0a5 5 0 0 1 5 5c0 3-5 8-5 8S0 8 0 5a5 5 0 0 1 5-5z" fill="#fff"/><circle cx="5" cy="5" r="2" fill="#333"/></svg>208 Heron Mill Road</li>
      <li style="padding-left:20px">Lakeport, FL</li>
      <li><svg width="12" height="12" viewBox="0 0 12 12"><path d="M2 0l3 3-1.5 2a7 7 0 0 0 3.5 3.5L9 7l3 3-2 2C5 12 0 7 0 2z" fill="#fff"/></svg>1 555 014 2290</li>
      <li><svg width="13" height="10" viewBox="0 0 13 10"><rect width="13" height="10" rx="1" fill="#fff"/><path d="M0 1l6.5 5L13 1" stroke="#333" fill="none"/></svg>info@gridwaveform-mail.com</li>
    </ul>
  </div>
  <div class="fcol" style="left:425px">
    <h4>Links</h4>
    <ul><li>Home</li><li>About us</li><li>Services</li><li>Blog</li><li>FAQ</li></ul>
  </div>
  <div class="fcol" style="left:599px">
    <h4>Support</h4>
    <ul><li>Terms &amp; Condition</li><li>Login</li><li>Register</li><li>Contact us</li></ul>
  </div>
  <div class="fcol" style="left:821px">
    <h4>Email Subscription</h4>
    <p style="font-size:13px;line-height:24px;width:230px">Register your email address to get information</p>
    <div class="sub-input">Email Address</div>
    <div class="btn" style="position:relative;width:105px;height:33px;font-size:12px;margin-top:22px">Subscribe</div>
  </div>
  <div class="abs copyright">Copyrights © 2018. Allrights Reserved.</div>
  <span class="abs social" style="left:995px;background:#3b5ea8"></span>
  <span class="abs social" style="left:1036px;background:#2aa3ef"></span>
  <span class="abs social" style="left:1076px;background:#c0392b"></span>
</footer>

</body>
</html>
```